Home Security Company Business Card

Looking for a eye catching business card that is non traditional and stands out but yet still looks professional. It should include all the pertinent information such as name, title, address, telephone, e-mail, website address should definitely stand out and then finally the logo.

Target Market(s)

Residential and Commercial accounts mostly upscale accounts

Industry/Entity Type

Security

Contact Information for Business Card

Name
Title
Address
Office #
Cell #
E-mail
Website

Font styles to use
Serif
Sans Serif

Requirements
Must have
• Logo, two sided color configuration
Nice to have
• You decide
Should not have
• There really aren't any.

```html
<!DOCTYPE html>
<html lang="en">
<head>
<meta charset="utf-8">
<title>Harborline Protection Co. – Business Card</title>
<link href="https://fonts.googleapis.com/css2?family=Open+Sans:wght@400;600;700&display=swap" rel="stylesheet">
<style>
  :root {
    --maroon: #7d1418;
    --maroon-deep: #5a0b0e;
    --maroon-light: #a3262c;
    --gold: #f0c258;
    --gold-deep: #d9a23a;
    --gold-text: #e8b64a;
    --paper: #ffffff;
    --backdrop: #ece8e2;
  }
  * { margin: 0; padding: 0; box-sizing: border-box; }
  html, body {
    width: 1200px; height: 913px; overflow: hidden;
    background: var(--backdrop);
    font-family: "Open Sans", Arial, sans-serif;
  }
  .stage {
    position: relative; width: 1200px; height: 913px;
    display: flex; align-items: center; justify-content: center; gap: 40px;
  }
  .card {
    position: relative; width: 520px; height: 300px;
    border-radius: 22px; overflow: hidden;
    box-shadow: 0 10px 28px rgba(0,0,0,0.18);
  }
  .card-front { background: var(--paper); }
  .card-back {
    background: linear-gradient(160deg, var(--maroon-light) 0%, var(--maroon) 45%, var(--maroon-deep) 100%);
  }
  .wave { position: absolute; inset: 0; width: 100%; height: 100%; }

  .brand { position: absolute; display: flex; align-items: center; gap: 10px; }
  .brand-dot { width: 40px; height: 40px; border-radius: 50%; background: var(--gold-deep); flex: none; }
  .brand-name { font-weight: 700; font-size: 17px; line-height: 1.15; letter-spacing: 0.5px; text-transform: uppercase; }
  .card-front .brand { left: 30px; top: 112px; }
  .card-front .brand-name { color: var(--maroon); }
  .card-back .brand { left: 150px; top: 110px; }
  .card-back .brand-name { color: var(--paper); font-size: 20px; }
  .card-back .brand-dot { width: 52px; height: 52px; background: var(--gold); }

  .identity { position: absolute; left: 300px; top: 28px; }
  .person-name { color: var(--maroon); font-weight: 700; font-size: 22px; }
  .person-title { color: var(--gold-text); font-weight: 600; font-size: 13px; margin-top: -2px; }

  .contacts { position: absolute; left: 300px; top: 86px; list-style: none; }
  .contacts li { display: flex; align-items: center; gap: 8px; color: var(--maroon); font-size: 13px; line-height: 20px; }
  .contacts svg { width: 12px; height: 12px; fill: var(--gold-deep); flex: none; }

  .address { position: absolute; left: 180px; bottom: 24px; color: var(--maroon); font-weight: 600; font-size: 14px; }

  .website { position: absolute; left: 150px; bottom: 60px; color: var(--gold); font-weight: 600; font-size: 16px; letter-spacing: 0.2px; }
</style>
</head>
<body>
<main class="stage">
  <section class="card card-front" aria-label="Card front">
    <svg class="wave" viewBox="0 0 520 300" preserveAspectRatio="none" aria-hidden="true">
      <defs>
        <linearGradient id="goldFill" x1="0" y1="0" x2="0" y2="1">
          <stop offset="0" stop-color="#f6d27a"/>
          <stop offset="1" stop-color="#e9b24a"/>
        </linearGradient>
      </defs>
      <path d="M0,300 L0,238 C160,242 255,180 355,163 C430,152 480,152 520,152 L520,300 Z" fill="var(--maroon)"/>
      <path d="M0,300 L0,250 C160,252 260,192 360,175 C435,164 482,164 520,164 L520,300 Z" fill="url(#goldFill)"/>
    </svg>

    <div class="brand">
      <span class="brand-dot"></span>
      <span class="brand-name">Harborline<br>Protection Co.</span>
    </div>

    <div class="identity">
      <h1 class="person-name">Daniel Whitmore</h1>
      <p class="person-title">Owner</p>
    </div>

    <ul class="contacts">
      <li><svg viewBox="0 0 12 12"><path d="M1 3h10v2H9V4H3v1H1zM2 6h8l1 5H1z"/></svg>+330 2461-5532</li>
      <li><svg viewBox="0 0 12 12"><path d="M2 1l2 0 1 3-1.5 1a7 7 0 0 0 3.5 3.5L8 7l3 1v2c0 1-1 1-1 1A9 9 0 0 1 1 2s0-1 1-1z"/></svg>+3302540-71245</li>
      <li><svg viewBox="0 0 12 12"><path d="M0 2h12v8H0zM1 3v.5l5 3.2 5-3.2V3z"/></svg>info@danielwhitmoremail.com</li>
    </ul>

    <p class="address">248 Meadow Lane Oakridge, Illinois 60455</p>
  </section>

  <section class="card card-back" aria-label="Card back">
    <div class="brand">
      <span class="brand-dot"></span>
      <span class="brand-name">Harborline<br>Protection Co.</span>
    </div>
    <p class="website">www.harborlineprotectionco.com</p>
  </section>
</main>
</body>
</html>
```